brovane business card

We are a commercial cleaning/janitorial service company our main target is building owners and managers.
Would like to see the icon as a background shadow in the front and the full logo in white on the back with a blue background.  On the card:
Dorn Hassel, Operations Manager, dorn@brovane-mail.com
48371-B Orchard Ln. 9 #402
Fenwick, OR 58217
555.304.8812, 800.555.4170

Updates
please include cell 555.618.2243
                                   
Thank you
If possible the fading logo on the front should be very subtle and light and lets look at centering that as well
thanks

Industry/Entity Type
Building
Look and feel
Each slider illustrates characteristics of the customer's brand and the style your logo design should communicate.

```html
<!DOCTYPE html>
<html lang="en">
<head>
<meta charset="utf-8">
<title>Brovane Business Card</title>
<link rel="stylesheet" href="https://fonts.googleapis.com/css2?family=PT+Sans:wght@400;700&family=Quicksand:wght@300&display=swap">
<style>
  :root {
    --stage: #3a3a3a;
    --blue-deep: #0f2b57;
    --blue-mid: #1d4f8f;
    --blue-light: #4f86c4;
    --paper: #f4f4f4;
    --paper-shade: #e2e2e2;
    --ink: #1d1d1d;
    --white: #ffffff;
    --brand-blue: #1f5aa8;
  }
  * { margin: 0; padding: 0; box-sizing: border-box; }
  html, body { width: 1200px; height: 900px; overflow: hidden; }
  body {
    background: var(--stage);
    font-family: "PT Sans", sans-serif;
    position: relative;
  }
  .set-title {
    position: absolute;
    top: 28px;
    right: 30px;
    font-family: "Quicksand", sans-serif;
    font-weight: 300;
    font-size: 46px;
    color: var(--white);
  }
  .card {
    position: absolute;
    width: 540px;
    height: 309px;
    overflow: hidden;
    box-shadow: 0 12px 30px rgba(0,0,0,.45);
  }
  .card--front {
    left: 60px;
    top: 230px;
    background: radial-gradient(ellipse at 45% 45%, var(--blue-light) 0%, var(--blue-mid) 40%, var(--blue-deep) 100%);
  }
  .card--back {
    left: 610px;
    top: 400px;
    background: linear-gradient(160deg, var(--white) 0%, var(--paper) 55%, var(--paper-shade) 100%);
    color: var(--ink);
  }
  .card__watermark {
    position: absolute;
    left: 50%;
    top: 50%;
    width: 300px;
    height: 300px;
    transform: translate(-50%, -50%);
    border-radius: 50%;
  }
  .card--front .card__watermark { background: rgba(255,255,255,.06); }
  .card--back .card__watermark { background: rgba(0,0,0,.035); }
  .brand {
    display: flex;
    align-items: center;
    gap: 14px;
    font-weight: 700;
  }
  .brand__dot { border-radius: 50%; flex: none; }
  .card--front .brand {
    position: absolute;
    left: 0; right: 0;
    top: 96px;
    justify-content: center;
    color: var(--white);
    font-size: 62px;
  }
  .card--front .brand__dot { width: 78px; height: 78px; background: var(--white); }
  .card__url {
    position: absolute;
    left: 0; right: 0;
    top: 222px;
    text-align: center;
    color: var(--white);
    font-size: 20px;
  }
  .card--back .brand {
    position: absolute;
    right: 40px;
    top: 40px;
    color: var(--brand-blue);
    font-size: 36px;
    gap: 10px;
  }
  .card--back .brand__dot { width: 44px; height: 44px; background: var(--brand-blue); }
  .person {
    position: absolute;
    left: 40px;
    top: 150px;
    text-align: right;
    width: 200px;
  }
  .person__name { font-size: 21px; }
  .person__role { font-size: 13px; margin-top: 2px; }
  .person__email { font-size: 14px; margin-top: 4px; }
  .contact {
    position: absolute;
    left: 262px;
    top: 150px;
    font-size: 19px;
    line-height: 1.2;
  }
  .contact__phones { margin-top: 26px; }
</style>
</head>
<body>
  <div class="set-title">Brovane</div>

  <section class="card card--front">
    <div class="card__watermark"></div>
    <div class="brand"><span class="brand__dot"></span><span class="brand__name">brovane</span></div>
    <div class="card__url">www.brovane-clean.com</div>
  </section>

  <section class="card card--back">
    <div class="card__watermark"></div>
    <div class="brand"><span class="brand__dot"></span><span class="brand__name">brovane</span></div>
    <div class="person">
      <div class="person__name">Dorn Hassel</div>
      <div class="person__role">Operations Manager</div>
      <div class="person__email">dorn@brovane-mail.com</div>
    </div>
    <div class="contact">
      <div class="contact__address">48371-B Orchard Ln. 9 #402<br>Fenwick, OR 58217</div>
      <div class="contact__phones">555.304.8812<br>800.555.4170</div>
    </div>
  </section>
</body>
</html>
```